At Home Pet Euthanasia - business cards & brand stationary

We already have a logo and the colors and a website. Need a business card designed that will be able to customized to multiple veterinarians who will be partnering with us. The feel needs to be compassionate, comforting with our tagline 'A Gift of Love at Home'. It will be 2 sides.
On the back our platform/partner vets will be customizing each business card with their own service areas, phone numbers, name and title. On the front, i would like to see experimentation with use of our photos, the logo, tagline and a description 'Peaceful and Compassionate At-Home Pet Euthanasia'

```html
<!DOCTYPE html>
<html lang="en">
<head>
<meta charset="utf-8">
<title>Tendra Pet – Business Card</title>
<link rel="stylesheet" href="https://fonts.googleapis.com/css2?family=Poppins:ital,wght@0,300;0,600;1,300&family=Arimo&family=EB+Garamond:ital@1&display=swap">
<style>
  :root {
    --backdrop: #262626;
    --card: #ffffff;
    --brand-blue: #7596c0;
    --ink: #111111;
    --rule: #9aa3ad;
    --photo-light: #d2d2d2;
    --photo-mid: #9a9a9a;
    --photo-dark: #4a4a4a;
    --headline: #ffffff;
  }
  * { margin: 0; padding: 0; box-sizing: border-box; }
  html, body { width: 1065px; height: 1200px; overflow: hidden; }
  body { background: var(--backdrop); position: relative; font-family: "Arimo", Arial, sans-serif; }

  .card { position: absolute; width: 583px; height: 362px; overflow: hidden; box-shadow: 3px 3px 4px rgba(0,0,0,.7); }

  /* Contact side */
  .card--contact { left: 292px; top: 218px; background: var(--card); border-radius: 0 181px 181px 0 / 0 181px 181px 0; }
  .brand { position: absolute; left: 376px; top: 286px; }
  .brand-lockup { position: absolute; left: 0; top: 0; width: 226px; height: 60px; transform-origin: 0 0; transform: translate(0, 226px) rotate(-90deg); display: flex; align-items: center; gap: 10px; }
  .brand-mark { width: 44px; height: 44px; background: var(--brand-blue); flex: none; }
  .brand-name { font-family: "Poppins", sans-serif; font-weight: 600; font-size: 38px; color: var(--brand-blue); line-height: 1; white-space: nowrap; }
  .tagline { position: absolute; left: 443px; top: 435px; transform-origin: 0 0; transform: rotate(-90deg); font-family: "Poppins", sans-serif; font-weight: 300; font-style: italic; font-size: 12.5px; color: var(--brand-blue); white-space: nowrap; }
  .divider { position: absolute; left: 189px; top: 94px; width: 1px; height: 174px; background: var(--rule); }

  .details { position: absolute; left: 213px; top: 92px; color: var(--ink); font-size: 16.5px; line-height: 21px; }
  .person-name { font-family: "Poppins", sans-serif; font-weight: 600; font-size: 21px; color: var(--brand-blue); line-height: 24px; }
  .person-title { line-height: 19px; }
  .contact-list { list-style: none; margin-top: 15px; }
  .contact-list li { display: flex; align-items: center; gap: 6px; }
  .contact-list svg { width: 15px; height: 15px; flex: none; }
  .accent { color: var(--brand-blue); }
  .address { margin-top: 13px; }

  /* Message side */
  .card--message { left: 264px; top: 623px; border-radius: 181px 0 0 181px / 181px 0 0 181px; }
  .photo { position: absolute; inset: 0; background:
      radial-gradient(ellipse at 30% 35%, var(--photo-mid) 0%, transparent 55%),
      radial-gradient(ellipse at 55% 75%, #e6e6e6 0%, transparent 45%),
      linear-gradient(100deg, var(--photo-dark) 0%, var(--photo-mid) 40%, var(--photo-light) 75%, #bdbdbd 100%); }
  .headline { position: absolute; left: 250px; top: 26px; width: 330px; text-align: center; font-family: "EB Garamond", Georgia, serif; font-style: italic; font-size: 26px; line-height: 37px; color: var(--headline); }
</style>
</head>
<body>

<section class="card card--contact">
  <div class="brand" style="left:84px; top:68px;">
    <div class="brand-lockup">
      <span class="brand-mark"></span>
      <span class="brand-name">Tendra Pet</span>
    </div>
  </div>
  <p class="tagline" style="left:151px; top:217px;">A gift of love at home.</p>
  <span class="divider"></span>

  <div class="details">
    <h1 class="person-name">Daniel Marsh</h1>
    <p class="person-title">Managing Director</p>
    <ul class="contact-list">
      <li>
        <svg viewBox="0 0 16 16" aria-hidden="true"><path d="M4 1.5 6 4 4.8 5.6c.8 2 2.3 3.6 4.3 4.5L10.6 9l2.6 2-1.1 2.6C7 13.3 2.7 9 2.4 3.9Z" fill="var(--brand-blue)"/><path d="M9.5 2.5a4 4 0 0 1 4 4M9.5 4.8a1.8 1.8 0 0 1 1.8 1.8" stroke="var(--brand-blue)" stroke-width="1.2" fill="none"/></svg>
        <span>055-240 318 642</span>
      </li>
      <li>
        <svg viewBox="0 0 16 16" aria-hidden="true"><rect x="1" y="3.5" width="14" height="9" fill="var(--brand-blue)"/><path d="M1 3.5 8 9l7-5.5" stroke="#fff" stroke-width="1" fill="none"/></svg>
        <span>hello@tendrapet.com</span>
      </li>
      <li>
        <svg viewBox="0 0 16 16" aria-hidden="true"><g stroke="var(--brand-blue)" stroke-width="1.1" fill="none"><circle cx="8" cy="8" r="6.5"/><ellipse cx="8" cy="8" rx="3" ry="6.5"/><path d="M1.5 8h13M2.5 4.8h11M2.5 11.2h11"/></g></svg>
        <span>www.<span class="accent">tendrapet</span>.com</span>
      </li>
    </ul>
    <p class="address">18, Willow Bend Road<br>30917, Fairhaven</p>
  </div>
</section>

<section class="card card--message">
  <div class="photo" role="img" aria-label="Black and white photograph of a person gently holding and kissing a tabby cat"></div>
  <p class="headline">Peaceful and Compassionate At-Home Pet Euthanasia</p>
</section>

</body>
</html>
```